4D Cradle Glimpse Luxury Ultrasound Billboard

Design a HIGH-END, MODERN billboard for my private prenatal ultrasound studio, 4D Cradle Glimpse, located in Pace, Florida.
This billboard will be viewed by drivers traveling at highway speeds, so it must be extremely clean, simple, and readable within 6 seconds.
About My Business
4D Cradle Glimpse is a private prenatal ultrasound studio specializing in:
Highest technology 4D/HD Ultrasounds
Early Gender Determination
Pregnancy Confirmation
I have been serving families for nearly 10 years and is known for creating a memorable experience, not just an ultrasound appointment.
Design Style
I DO NOT want:
Flowers
Leaves
Swirls
Glitter
Hearts everywhere
Busy backgrounds
Generic maternity stock graphics
I DO want:
Modern
Luxury
Upscale
Clean
Professional
Eye-catching
Premium medical spa feel
Colors
Use colors from my logo:
LOGO Green ( or a deep green)
Black
White
Soft Gold accents
Images:
Incorporate my professional headshot in a clean, modern way, logo, and the ultrasound images
Text
Keep wording minimal.
Primary Headline ( OPEN TO IDEAS) :
EXAMPLES ( WOULD RATHER SOMETHING MORE CATCHY)
" ADVANCED IMAGING. UNFORGETTABLE MOMENTS"
"MEET YOUR BABY BEFORE BIRTH"
Under headline:
4D Ultrasound • Early Gender • Pregnancy Confirmation
Business Name:
4D Cradle Glimpse
Private Prenatal Ultrasound Studio
Phone Number:
850-471-5923
Important
This billboard must be readable in 5–6 seconds from a moving vehicle.
Less text is better.
The phone number and business name must be visible from a distance.
The design should feel like a premium brand that immediately tells expecting parents:
“This is where I go to see my baby.”
Files Provided
Official logo
Headshot
Ultrasound images
Don’t make this look like a medical office billboard.
Make it look like a luxury baby experience billboard. That’s what separates 4D Cradle Glimpse from hospitals, OB offices, and all the new studios popping up around you. The emotional connection is what gets moms to book. ❤️
Billboard Size - 10.6” x 36”

```html
<!DOCTYPE html>
<html lang="en">
<head>
<meta charset="utf-8">
<title>4D Cradle Glimpse Billboard</title>
<link rel="stylesheet" href="https://fonts.googleapis.com/css2?family=Noto+Serif:wght@700&family=Roboto:wght@500;700;900&display=swap">
<style>
:root{
  --green-deep:#0f221b;
  --green-mid:#17302a;
  --gold:#c2922c;
  --gold-soft:#e0b24a;
  --white:#ffffff;
  --logo-green:#4a5a50;
  --skin-dark:#6e3226;
  --skin-light:#b8705e;
}
*{margin:0;padding:0;box-sizing:border-box}
html,body{width:1200px;height:375px;overflow:hidden;background:var(--green-deep)}
.billboard{position:relative;width:1200px;height:375px;overflow:hidden;
  background:linear-gradient(180deg,var(--green-mid),var(--green-deep));font-family:"Roboto",sans-serif}
.phone-band{position:absolute;left:360px;top:323px;width:840px;height:52px;background:var(--gold)}
.ultrasound{position:absolute;left:0;top:0;width:420px;height:375px}
.headline{position:absolute;left:413px;top:44px;width:540px;text-align:center;font-family:"Noto Serif",serif;font-weight:700;line-height:1;white-space:nowrap}
.headline .line-one{display:block;color:var(--white);font-size:50px;letter-spacing:.5px}
.headline .line-two{display:block;color:var(--gold);font-size:57px;margin-top:12px;letter-spacing:0}
.divider{position:absolute;left:527px;top:176px;width:300px;height:20px}
.tagline{position:absolute;left:433px;top:206px;width:500px;text-align:center;font-family:"Noto Serif",serif;font-weight:700;color:var(--white);font-size:16.5px;letter-spacing:.3px;white-space:nowrap}
.services{position:absolute;left:445px;top:253px;display:flex;align-items:center}
.service{display:flex;align-items:center;color:var(--white);font-weight:500;font-size:12.5px;letter-spacing:.4px;line-height:1.35;white-space:nowrap}
.service svg{width:37px;height:37px;margin-right:11px;flex:none}
.service.ultra{width:177px}
.service.gender{width:172px}
.headshot{position:absolute;left:995px;top:24px;width:183px;height:183px;border-radius:50%;border:3px solid var(--gold);
  background:radial-gradient(circle at 55% 40%,#e8dccb 0%,#c9b596 35%,#41533f 75%,#2d3b30 100%)}
.brand-card{position:absolute;left:990px;top:219px;width:184px;height:91px;background:var(--white);border-radius:9px;border:2px solid #9aa59c;
  display:flex;flex-direction:column;align-items:center;justify-content:center}
.brand-card .brand-name{font-family:"Noto Serif",serif;font-weight:700;color:var(--gold);font-size:17px;line-height:1.1;text-align:center;white-space:nowrap}
.brand-card .brand-rule{width:150px;height:1px;background:var(--gold);margin:8px 0 5px}
.brand-card .brand-sub{font-size:7.5px;font-weight:500;color:var(--logo-green);letter-spacing:.5px;white-space:nowrap}
.contact{position:absolute;left:416px;top:323px;height:52px;display:flex;align-items:center}
.contact .phone-icon{width:40px;height:40px;margin-right:17px}
.contact .number{font-weight:900;color:var(--white);font-size:44px;letter-spacing:1px;line-height:1;white-space:nowrap}
.band-name{position:absolute;left:792px;top:323px;height:52px;display:flex;align-items:center;color:var(--white);font-weight:700;font-size:14.5px;letter-spacing:.2px;white-space:nowrap}
</style>
</head>
<body>
<div class="billboard">
  <div class="phone-band"></div>

  <svg class="ultrasound" viewBox="0 0 420 375" role="img" aria-label="4D ultrasound image of twin babies face to face">
    <defs>
      <radialGradient id="scanTone" cx="45%" cy="45%" r="70%">
        <stop offset="0" stop-color="#b8705e"/>
        <stop offset="0.6" stop-color="#8e4a3b"/>
        <stop offset="1" stop-color="#6e3226"/>
      </radialGradient>
    </defs>
    <path d="M0 0 H335 Q460 187 326 375 H0 Z" fill="url(#scanTone)"/>
    <path d="M335 0 Q460 187 326 375" fill="none" stroke="#e0b24a" stroke-width="3"/>
  </svg>

  <h1 class="headline">
    <span class="line-one">MEET YOUR BABY</span>
    <span class="line-two">BEFORE BIRTH</span>
  </h1>

  <svg class="divider" viewBox="0 0 300 20">
    <line x1="0" y1="10" x2="137" y2="10" stroke="#c2922c" stroke-width="1.5"/>
    <line x1="163" y1="10" x2="300" y2="10" stroke="#c2922c" stroke-width="1.5"/>
    <path d="M150 1 Q151.5 8.5 159 10 Q151.5 11.5 150 19 Q148.5 11.5 141 10 Q148.5 8.5 150 1Z" fill="#e0b24a"/>
  </svg>

  <p class="tagline">LUXURY 4D IMAGING EXPERIENCE</p>

  <div class="services">
    <div class="service ultra">
      <svg viewBox="0 0 37 37"><circle cx="18.5" cy="18.5" r="17" fill="none" stroke="#c2922c" stroke-width="1.6"/>
        <circle cx="18.5" cy="18.5" r="8" fill="none" stroke="#c2922c" stroke-width="1.4"/>
        <circle cx="17" cy="15.5" r="2.6" fill="#c2922c"/></svg>
      <span>4D ULTRASOUND</span>
    </div>
    <div class="service gender">
      <svg viewBox="0 0 37 37"><circle cx="18.5" cy="18.5" r="17" fill="none" stroke="#c2922c" stroke-width="1.6"/>
        <circle cx="15" cy="17" r="5" fill="none" stroke="#c2922c" stroke-width="1.5"/>
        <line x1="15" y1="22" x2="15" y2="28" stroke="#c2922c" stroke-width="1.5"/>
        <line x1="12" y1="25.5" x2="18" y2="25.5" stroke="#c2922c" stroke-width="1.5"/>
        <circle cx="21" cy="16" r="5" fill="none" stroke="#c2922c" stroke-width="1.5"/>
        <path d="M24.5 12.5 L28 9 M24.5 9 H28 V12.5" fill="none" stroke="#c2922c" stroke-width="1.5"/></svg>
      <span>EARLY GENDER</span>
    </div>
    <div class="service confirm">
      <svg viewBox="0 0 37 37"><circle cx="18.5" cy="18.5" r="17" fill="none" stroke="#c2922c" stroke-width="1.6"/>
        <path d="M14 9 Q10 18 15 28 M23 9 Q27 18 22 28" fill="none" stroke="#c2922c" stroke-width="1.4"/>
        <circle cx="18.5" cy="19" r="4" fill="none" stroke="#c2922c" stroke-width="1.4"/></svg>
      <span>PREGNANCY<br>CONFIRMATION</span>
    </div>
  </div>

  <div class="headshot" role="img" aria-label="Professional headshot of the studio owner"></div>

  <div class="brand-card">
    <span class="brand-name">4D Cradle Glimpse</span>
    <span class="brand-rule"></span>
    <span class="brand-sub">PRENATAL ULTRASOUND STUDIO</span>
  </div>

  <div class="contact">
    <svg class="phone-icon" viewBox="0 0 40 40"><circle cx="20" cy="20" r="20" fill="#ffffff"/>
      <path d="M13 11 L17 10.5 L19 16 L16.5 17.8 Q18.5 22 22.2 23.5 L24 21 L29.5 23 L29 27 Q28 29.5 25 29 Q15 27 11 16 Q10.5 12 13 11Z" fill="#c2922c"/></svg>
    <span class="number">850-471-5923</span>
  </div>
  <div class="band-name">4D Cradle Glimpse Private Prenatal Ultrasound Studio</div>
</div>
</body>
</html>
```